Design a poster that illustrates the six central pillars of our school district's efforts with students. The attached PDF outlines the six main competencies we aim for students to possess upon graduation. Each of the 6 has 3 bullet points for the poster as well. The title is "Profile of a Trailblazer". Our mascot is this attached winged wheel. The overall concept is that staff take kids when they are young and develop these 6 things when they graduate. Our colors are navy, red, and white. We will make this poster in a variety of sizes in offices, classrooms, and in digital spaces as well. On the PDF - ignore the column that says "Synthesis". That has nothing to do with this poster.

The district is Harlow Creek Public Schools https://www.harlowcreek-schools.example/

```html
<!DOCTYPE html>
<html lang="en">
<head>
<meta charset="utf-8">
<title>Profile of a Trailblazer – Harlow Creek Public Schools</title>
<link rel="stylesheet" href="https://fonts.googleapis.com/css2?family=Bubblegum+Sans&family=Jost:wght@500;700&display=swap">
<style>
  :root {
    --navy: #0e0f3d;
    --red: #a51e26;
    --white: #ffffff;
    --ink: #1d1b38;
  }
  * { box-sizing: border-box; margin: 0; padding: 0; }
  html, body { width: 884px; height: 1200px; overflow: hidden; background: var(--navy); }
  .poster { position: relative; width: 884px; height: 1200px; background: var(--navy); }
  .frame {
    position: absolute; left: 67px; top: 60px; width: 750px; height: 1080px;
    background: var(--white); border: 10.5px solid var(--red); border-radius: 34px;
  }
  .brand {
    position: absolute; left: 78px; width: 728px; top: 140px;
    display: flex; align-items: center; justify-content: center; gap: 12px;
    font-family: "Bubblegum Sans", cursive; font-size: 34px; color: var(--red);
  }
  .brand-dot { width: 26px; height: 26px; border-radius: 50%; background: var(--navy); }
  .title-band {
    position: absolute; left: 78px; top: 246px; width: 728px; height: 71px;
    background: var(--red); display: flex; align-items: center; justify-content: center;
  }
  .title {
    font-family: "Jost", sans-serif; font-weight: 700; font-size: 47px; color: var(--white);
    letter-spacing: -0.5px; white-space: nowrap;
  }
  .grades-tag {
    position: absolute; left: 491px; top: 325px; width: 326px; height: 40px;
    background: var(--navy); border-radius: 22px 0 0 22px;
    display: flex; align-items: center; padding-left: 29px;
    font-family: "Jost", sans-serif; font-weight: 500; font-size: 30px;
    color: var(--white); letter-spacing: 3px;
  }
  .path-lines { position: absolute; left: 0; top: 0; width: 884px; height: 1200px; }
  .mini-brand {
    position: absolute; font-family: "Bubblegum Sans", cursive; font-size: 15px;
    color: var(--navy); display: flex; align-items: center; gap: 5px; white-space: nowrap;
  }
  .mini-brand .brand-dot { width: 10px; height: 10px; }
  .pillar-name {
    position: absolute; font-family: "Bubblegum Sans", cursive; font-size: 25px;
    color: var(--navy); line-height: 1; transform: translateY(-50%); white-space: nowrap;
  }
  .pillar-points {
    position: absolute; list-style: none;
    font-family: "Bubblegum Sans", cursive; font-size: 18px; line-height: 21.5px;
    color: var(--ink); white-space: nowrap;
  }
  .pillar-points li { padding-left: 12px; text-indent: -12px; }
  .pillar-points li::before { content: "•"; display: inline-block; width: 12px; text-indent: 0; }
</style>
</head>
<body>
<main class="poster">
  <div class="frame"></div>

  <div class="brand"><span class="brand-dot"></span>Harlow Creek Public Schools</div>

  <div class="title-band"><h1 class="title">Profile of a TRAILBLAZER</h1></div>
  <div class="grades-tag">GRADES 5–12</div>

  <svg class="path-lines" viewBox="0 0 884 1200" aria-hidden="true">
    <g fill="none" stroke="#a51e26" stroke-width="3.5" stroke-linecap="round">
      <path d="M198 408 H532"/>
      <path d="M685 408 H701 A52.5 52.5 0 0 1 701 513 H332"/>
      <path d="M171 513 A52.5 52.5 0 0 0 171 618 H530"/>
      <path d="M662 618 H701 A52 52 0 0 1 701 722 H282"/>
      <path d="M171 722 A58.5 58.5 0 0 0 171 839 H530"/>
      <path d="M669 839 H701 A52.5 52.5 0 0 1 701 944 H333"/>
      <path d="M171 944 A53 53 0 0 0 171 1050 H626"/>
    </g>
  </svg>

  <div class="mini-brand" style="left:118px; top:378px;"><span class="brand-dot"></span>Harlow Creek</div>
  <div class="mini-brand" style="left:640px; top:1056px;"><span class="brand-dot"></span>Harlow Creek</div>

  <section>
    <h2 class="pillar-name" style="left:538px; top:408px;">Communicator</h2>
    <ul class="pillar-points" style="left:206px; top:424px;">
      <li>Expresses ideas clearly and respectfully (written &amp; verbal).</li>
      <li>Listens actively and understands diverse perspectives.</li>
      <li>Adjusts communication to suit the audience and context.</li>
    </ul>
  </section>

  <section>
    <h2 class="pillar-name" style="left:179px; top:513px;">Critical Thinker</h2>
    <ul class="pillar-points" style="left:156px; top:530px;">
      <li>Questions, analyzes, and evaluates information from multiple sources.</li>
      <li>Identifies and solves complex problems creatively.</li>
      <li>Uses evidence and diverse perspectives to form reasoned conclusions<br>and make informed decisions</li>
    </ul>
  </section>

  <section>
    <h2 class="pillar-name" style="left:538px; top:618px;">Responsible</h2>
    <ul class="pillar-points" style="left:206px; top:639px;">
      <li>Takes ownership of actions, choices, and commitments.</li>
      <li>Manages time, resources, and self to meet expectations.</li>
      <li>Acts with integrity and advocates for self and others.</li>
    </ul>
  </section>

  <section>
    <h2 class="pillar-name" style="left:179px; top:722px;">Adaptable</h2>
    <ul class="pillar-points" style="left:156px; top:743px;">
      <li>Responds productively to new situations, challenges, and feedback.</li>
      <li>Learns from new experiences and applies prior knowledge in evolving contexts.</li>
      <li>Adjusts behavior and approach to effectively engage with<br>diverse groups and environments.</li>
    </ul>
  </section>

  <section>
    <h2 class="pillar-name" style="left:538px; top:839px;">Collaborator</h2>
    <ul class="pillar-points" style="left:190px; top:861px;">
      <li>Contributes effectively and cooperatively to shared goals</li>
      <li>Listens actively and values diverse ideas and perspectives.</li>
      <li>Engages respectfully, compromising and leading when appropriate</li>
    </ul>
  </section>

  <section>
    <h2 class="pillar-name" style="left:179px; top:944px;">Compassionate</h2>
    <ul class="pillar-points" style="left:156px; top:964px; line-height:24.5px;">
      <li>Understands and acknowledges others' feelings, perspectives, and experiences.</li>
      <li>Responds with kindness, patience, and support.</li>
      <li>Seeks to connect with and contribute positively to the well-being of others</li>
    </ul>
  </section>
</main>
</body>
</html>
```